New Business Card Design Project

Need a design that will create an impact / strong impression towards our clients for our business. We are in the lighting business and we do lighting retrofits for large commercial to industrial clientele.

Target Market(s)

Lighting Industry

Industry/Entity Type

Business

Font styles to use
Other font styles liked:
• we would like to use the font on our logo, not sure what it is though..

Requirements
Must have
• Our logo.
Nice to have
• We are open to suggestions that have to do with lighting.

```html
<!DOCTYPE html>
<html lang="en">
<head>
<meta charset="utf-8">
<title>Lumora Retrofit Group – Business Card</title>
<link rel="stylesheet" href="https://fonts.googleapis.com/css2?family=Montserrat:wght@400;500;700&display=swap">
<style>
  :root {
    --bg: #e9ebea;
    --green-deep: #0c4a1c;
    --green-dark: #11601f;
    --green-mid: #128a3f;
    --green-light: #6cc24a;
    --text-grey: #6a6a6a;
    --white: #ffffff;
  }
  * { box-sizing: border-box; margin: 0; padding: 0; }
  html, body {
    width: 1200px; height: 930px; overflow: hidden;
    background: var(--bg);
    font-family: "Montserrat", sans-serif;
  }
  .stage {
    width: 1200px; height: 930px;
    display: flex; flex-direction: column; align-items: center; justify-content: center;
    gap: 40px;
  }
  .card {
    position: relative;
    width: 620px; height: 354px;
    border-radius: 16px;
    overflow: hidden;
    box-shadow: 0 10px 28px rgba(0,0,0,.18);
  }
  /* back */
  .card-back {
    background: radial-gradient(ellipse at 50% 30%, var(--green-dark), var(--green-deep) 80%);
    display: flex; flex-direction: column; align-items: center; justify-content: center;
  }
  .wordmark {
    display: flex; align-items: center; gap: 12px;
    font-weight: 700; color: var(--white);
  }
  .wordmark-square { width: 22px; height: 22px; background: var(--green-light); }
  .card-back .wordmark-name { font-size: 34px; letter-spacing: 1px; }
  .card-back .website {
    position: absolute; bottom: 46px; left: 0; right: 0; text-align: center;
    color: var(--white); font-size: 15px; letter-spacing: 1.5px;
  }
  /* front */
  .card-front { background: var(--white); }
  .card-front .wordmark {
    position: absolute; top: 44px; left: 40px; color: var(--green-dark);
  }
  .card-front .wordmark-name { font-size: 24px; letter-spacing: .5px; }
  .card-front .wordmark-square { width: 16px; height: 16px; }
  .person {
    position: absolute; top: 108px; right: 44px; text-align: right;
  }
  .person-name { color: var(--green-mid); font-size: 22px; font-weight: 500; }
  .person-title { color: var(--text-grey); font-size: 16px; margin-top: 2px; }
  .rule-top {
    position: absolute; top: 170px; right: 40px; width: 300px; height: 1.5px; background: var(--green-light);
  }
  .address {
    position: absolute; top: 182px; right: 44px; text-align: right;
    color: var(--text-grey); font-size: 14px; line-height: 1.5;
  }
  .rule-bottom {
    position: absolute; top: 232px; left: 40px; width: 170px; height: 1.5px; background: var(--green-light);
  }
  .contacts {
    position: absolute; top: 244px; left: 40px; list-style: none;
    color: var(--text-grey); font-size: 14px;
  }
  .contacts li { display: flex; align-items: center; gap: 10px; line-height: 1.65; }
  .contacts svg { width: 12px; height: 12px; fill: var(--green-mid); }
  .wave { position: absolute; left: 0; bottom: 0; width: 620px; height: 354px; }
</style>
</head>
<body>
<main class="stage">
  <section class="card card-back">
    <div class="wordmark">
      <span class="wordmark-square"></span>
      <span class="wordmark-name">Lumora Retrofit Group, LLC.</span>
    </div>
    <p class="website">www.lumoragroup.com</p>
  </section>

  <section class="card card-front">
    <svg class="wave" viewBox="0 0 620 354" aria-hidden="true">
      <path d="M200 354 C360 340 420 290 480 272 C540 254 580 250 620 246 L620 354 Z" fill="var(--green-light)"/>
      <path d="M214 354 C370 344 430 298 490 281 C545 265 585 261 620 257 L620 354 Z" fill="var(--white)"/>
      <path d="M222 354 C375 347 435 304 495 288 C550 273 588 269 620 266 L620 354 Z" fill="var(--green-mid)"/>
    </svg>

    <div class="wordmark">
      <span class="wordmark-square"></span>
      <span class="wordmark-name">Lumora Retrofit Group, LLC.</span>
    </div>

    <div class="person">
      <p class="person-name">DANIEL REYES</p>
      <p class="person-title">Founder</p>
    </div>
    <div class="rule-top"></div>
    <p class="address">4870 Meadow Lane,<br>Suite Tempe 85281</p>

    <div class="rule-bottom"></div>
    <ul class="contacts">
      <li><svg viewBox="0 0 12 12"><path d="M2.5 1 L4.5 1 L5.2 3.5 L4 4.5 C4.6 6 6 7.4 7.5 8 L8.5 6.8 L11 7.5 L11 9.5 C11 10.3 10.3 11 9.5 11 C5 11 1 7 1 2.5 C1 1.7 1.7 1 2.5 1 Z"/></svg>0400 555 019</li>
      <li><svg viewBox="0 0 12 12"><path d="M1 2.5 H11 V9.5 H1 Z M1 2.5 L6 6.5 L11 2.5" stroke="var(--white)" stroke-width=".8"/></svg>info@lumoragroup.com</li>
      <li><svg viewBox="0 0 12 12"><circle cx="6" cy="6" r="5"/></svg>www.lumoragroup.com</li>
    </ul>
  </section>
</main>
</body>
</html>
```